Generate website for parcelnook.com

Please design a website for our business. It must be clean, streamlined and obvious.

Our business combines ecommerce, with social networking, and zorvi maps. The logo is a shopping bag (ecommerce) and honeycombs inside representing the various compartments of business that are offered throughout site.

Clients use our site to visit the interior of stores and restaurants through video streaming and can virtually "walk through" the store and purchase items with friends and loved ones through the web.

We want to incorporate this logo with the work that we are doing and play on this honeycomb theme.

Our business is "parcelnook.com" because we are all about "u"!

Please make homepage with about us tab, contact us form, mission tab, we also want a page with our research links included that bolster the case for our startup.

We will incorporate a small video on the front screen. A homepage like fildrawer.com only this time with our parcelnook!

Also include, COMING SOON, on the homepage please.
Updates

These are some good templates/example sites of clean and simple but effective: https://7elmrow.com/preview www.fildrawer.com

We are excited to see your submissions. Currently, a very good and only one designer has posted so far. Let us know!

Please include the TM (trademark) symbol after the logo, the name, and the slogan throughout the website. Thank you!

Put the TM after the LOGO and after the slogan "Placement ran Supreme" Lorcan

Target Market(s)

We will begin with female online shoppers.

Industry/Entity Type

Shopping

Font styles to use
Serif
Sans Serif

Colors
e567a6
fece3e
85cae6

Requirements
Must have
• Clean Look
Simple like Fildrawer with simple options "see film" or login/signup.

With browser tabs at the bottom much like fildrawer.

1. Shopper when opening Parcelnook.com website will see a simple webpage with a large Parcelnook logo in the center.

2. User will see log-in and password or create account in upper right hand corner of webpage. Mobile device website will be underneath logo.

3.We Prefer a background for webpages adding a softer experience on the the eyes of the user. A photo in the background to show shopretail experience.

4. Clicking on theParcelnook logo will inform users of details and instructions about platform. Example: About, contact, mission, Help etc. Logo will become somewhat like an interactive tool for help and guidance.

5. Parcelnook is currently scouting for it's founding venues. A founding venue will be the first venues to appear to the public on the Parcelnook platform. Founding venues (FV) will inherit a lifetime of the lowest possible rates of 2%* for the duration of it's business. All businesses wishing to participate in the founding venues offer please leave your email address and store name and a representative will get back with you.

*Venues will be subjected to credit card and CoinTrail rates in addition.

Nice to have
• http://www.zorvi.com/patents/US5193774

Must include the link above/visual of this page on the site as well.

```html
<!DOCTYPE html>
<html lang="en">
<head>
<meta charset="utf-8">
<title>Parcelnook</title>
<link rel="stylesheet" href="https://fonts.googleapis.com/css2?family=Arimo:wght@400;700&family=Cinzel:wght@400;600&display=swap">
<style>
  :root {
    --page: #ffffff;
    --ink: #111111;
    --rule: #9a9a9a;
    --nav-shadow: rgba(0,0,0,0.28);
    --hero-light: #e7b877;
    --hero-mid: #c48a45;
    --hero-dark: #7a5a3c;
    --hero-cool: #c9c4bc;
    --glass: rgba(255,255,255,0.32);
    --white: #ffffff;
    --gold-top: #e7a83a;
    --gold-mid: #d68d1f;
    --gold-bottom: #b8731a;
    --button-edge: #e0e0e0;
  }
  * { box-sizing: border-box; margin: 0; padding: 0; }
  html, body { width: 1200px; height: 1091px; overflow: hidden; }
  body { position: relative; background: var(--page); font-family: "Arimo", Arial, sans-serif; color: var(--ink); }

  .site-nav {
    position: absolute; left: 0; top: 0; width: 1200px; height: 76px;
    background: var(--page); box-shadow: 0 4px 5px var(--nav-shadow);
  }
  .site-nav a {
    position: absolute; top: 36px; font-size: 20px; color: var(--ink);
    text-decoration: none; transform: translateX(-50%);
  }

  .hero { position: absolute; left: 0; top: 128px; width: 1200px; height: 780px; overflow: hidden; }
  .hero-photo {
    position: absolute; inset: 0;
    background:
      radial-gradient(ellipse at 70% 25%, var(--hero-cool) 0%, transparent 45%),
      radial-gradient(ellipse at 25% 80%, var(--hero-dark) 0%, transparent 40%),
      linear-gradient(160deg, var(--hero-light) 0%, var(--hero-mid) 55%, var(--hero-light) 100%);
  }

  .brand { position: absolute; left: 311px; top: 139px; display: flex; align-items: flex-end; gap: 20px; }
  .brand-mark { width: 116px; height: 116px; background: var(--white); border-radius: 6px; }
  .brand-name { font-family: "Arimo", sans-serif; font-weight: 700; font-size: 62px; line-height: 1; color: var(--white); margin-bottom: 6px; }
  .brand-slogan {
    position: absolute; left: 670px; top: 318px; transform: translateX(-50%);
    font-family: "Arimo", sans-serif; font-size: 22px; color: var(--ink);
    background: var(--white); padding: 1px 8px; border-radius: 4px; white-space: nowrap;
  }

  .cta-heading {
    position: absolute; top: 368px; width: 520px; transform: translateX(-50%);
    text-align: center; font-family: "Cinzel", serif; font-size: 44px; line-height: 52px;
    color: var(--white); text-shadow: 0 2px 4px rgba(0,0,0,0.45);
  }
  .cta-divider { position: absolute; left: 611px; top: 376px; width: 2px; height: 244px; background: var(--white); }

  .cta-panel {
    position: absolute; top: 482px; height: 143px; border: 3px solid var(--white);
    border-radius: 14px; background: var(--glass);
  }
  .cta-panel p {
    position: absolute; left: 0; right: 0; top: 8px; text-align: center;
    font-family: "Cinzel", serif; font-size: 27px; color: var(--white);
    text-shadow: 0 1px 3px rgba(0,0,0,0.4);
  }
  .cta-button {
    position: absolute; top: 51px; height: 69px; border: 3px solid var(--button-edge);
    border-radius: 3px; background: linear-gradient(180deg, var(--gold-top), var(--gold-mid) 55%, var(--gold-bottom));
    font-family: "Cinzel", serif; font-size: 28px; color: var(--white);
    display: flex; align-items: center; justify-content: center;
    box-shadow: 2px 3px 4px rgba(0,0,0,0.35);
  }

  .founding-note {
    position: absolute; left: 0; width: 1200px; top: 966px; text-align: center;
    font-size: 21px; line-height: 33px; word-spacing: 18px; letter-spacing: 1px; color: var(--ink);
  }
  .footer-rule { position: absolute; left: 64px; width: 1096px; top: 1037px; height: 1px; background: var(--rule); }
  .copyright { position: absolute; left: 0; width: 1200px; top: 1048px; text-align: center; font-size: 14px; color: var(--ink); }
</style>
</head>
<body>
  <nav class="site-nav">
    <a href="#about" style="left:188px">About</a>
    <a href="#mission" style="left:453px">Mission</a>
    <a href="#coming-soon" style="left:762px">Coming soon</a>
    <a href="#contact" style="left:1036px">Contact us</a>
  </nav>

  <section class="hero">
    <div class="hero-photo" role="img" aria-label="Background photo of a multi-level retail store interior with shoppers, clothing displays and escalators"></div>

    <div class="brand">
      <div class="brand-mark"></div>
      <div class="brand-name">Parcelnook</div>
    </div>
    <div class="brand-slogan">Placement ran Supreme</div>

    <h2 class="cta-heading" style="left:347px">Sign up to Join the Shopping</h2>
    <div class="cta-divider"></div>
    <h2 class="cta-heading" style="left:873px">Request or Become a participating store</h2>

    <div class="cta-panel" style="left:118px; width:467px">
      <p>Enroll here to shop</p>
      <div class="cta-button" style="left:32px; width:417px">Enter Your Email Address</div>
    </div>
    <div class="cta-panel" style="left:636px; width:467px">
      <p>Enroll or nominate a shop</p>
      <div class="cta-button" style="left:77px; width:317px">Store Information</div>
    </div>
  </section>

  <p class="founding-note">FOUNDING VENUES WILL INHERIT A 2% LIFETIME FEE*<br>LIMITED TO A SELECT FEW</p>
  <div class="footer-rule"></div>
  <p class="copyright">©2014 · Parcelnook.com LLC. All Rights Reserved. Under Use and Authority of USPTO Patent# 5193774.</p>
</body>
</html>
```